New Corporate Email Signature with Custom GIF KAV Electric LLC & KAV Fire & Security

Project Overview
KAV Electric LLC and KAV Fire & Security are seeking a professional, polished, and technically robust corporate email signature design. The project has two integrated deliverables:
A custom animated GIF representing both sides of our business
A complete corporate email signature layout designed for real-world compatibility (Gmail, Outlook, iOS, Android)
Our brand aesthetic is corporate, conservative, and clean. We value clarity, trust, professionalism, and subtle creativity β€” nothing overly flashy or cartoonish.
This design will be used across the entire company and must be visually aligned with our brand while remaining technically dependable.

PART 1 β€” Animated GIF Requirements
The GIF will be the core visual anchor of the new signature.
It must be clean, smooth, subtle, and optimized for email use.
βš™ Technical Requirements
Max file size: 150–200 KB (smaller is better)
Dimensions: approx 300px width (flexible, but must look good small)
Looping: continuous loop
Style: professional, minimalistic transitions

No rapid flashing or harsh animations
Must export cleanly into a format email clients accept

🎞 GIF Animation Sequence
Phase 1 β€” KAV Electric (KE)
Use the yellow β€œKE” avatar logo (provided).
Animation flow:
KE avatar appears
Full name β€œKAV Electric LLC” slides in, fades in, or otherwise appears smoothly
A scrolling or cycling list of service offerings displays:
EV Charging Stations
Generator & Transformers
Testing & Troubleshooting
LED Lighting Upgrades
After the list is shown, the entire KE segment fades out

Phase 2 β€” KAV Fire & Security (KF)
Use the red β€œKF” avatar logo (provided).
Animation flow mirrors Phase 1:
KF avatar appears
Full name β€œKAV Fire & Security” slides/fades in
Scrolling or cycling list of services displays:
Fire Alarm Upgrades
BQTL 48 Test & Inspect
Security Surveillance Systems
Access Control Systems
Data & Fiber Optic Cabling
Fade out β†’ loop back to KE
Creative Direction

Designers are encouraged to use:
Clean transitions
Soft fades
Professional typography
Modern minimalism
Consistent brand colors
High clarity at small sizes

Avoid:
Busy motion
Hard flashes
Excessive text overlays
Overly long transitions

The goal: a smooth, corporate-grade rotation that fits seamlessly into an email signature.

PART 2 β€” Corporate Email Signature Design

The signature must be visually appealing, brand-aligned, and structurally bulletproof across all major email systems.
πŸ“ Required Elements
πŸ‘€ Left Side Content
Circular headshot (we will supply final photos)
Social media icons with embedded URLs:
Facebook
LinkedIn
Google Business Profile
Instagram

Icons should be clean, modern, and in alignment with brand colors
πŸ“„ Right Side Content
Name
Title
KAV Electric LLC / KAV Fire & Security (depending on user)
Phone number
Email address
License# 52804
Physical office address: 384 Pembrook St, Westwood NJ 07912

Small CTA for newsletter signup (button or micro-banner)

🏒 Branding Assets Provided

You will receive:
KE avatar logo
KF avatar logo
Full-name KE logo
Full-name KF logo

These should be incorporated naturally and professionally.

Design Requirements

Conservative corporate styling

Clean typography

Balanced use of white space

Professional hierarchy

Light and dark mode compatibility preferred

Layout should not rely on one large image

All images should export cleanly for hosting on servers/CDN

Avoid overly tall signatures

The final signature must present as modern, trustworthy, and technically reliable across platforms.

πŸ§ͺ Compatibility Requirements

The signature must display correctly in:

Gmail (web and mobile)

Outlook (desktop & online)

Apple Mail

iPhone Mail

Android mail apps

Designers must avoid DIV-based layouts and instead propose a layout that can be implemented using table-based HTML, which is the industry standard for email compatibility.

You do not need to build the HTML β€” only supply the final layered design (PSD/AI/Figma) plus a clear structural layout that can be converted to HTML later.

πŸ“¦ Deliverables
1. Animated GIF

Final optimized GIF

Source file (After Effects, Photoshop, or equivalent)

Export guidelines so we can reproduce future versions

2. Email Signature Design

Full static design mockup

Modular layout for each employee

Icon set for social media

Newsletter CTA element

Clear spacing, alignment, and typography specifications

All source files (PSD, AI, Figma, etc.)

🧭 Creative Guidance Summary

We want:
βœ” Modern
βœ” Corporate
βœ” Minimalistic
βœ” Professional
βœ” Clean motion
βœ” Consistent branding
βœ” Email-safe elements

We do not want:
✘ Flashy marketing look
✘ Overly colorful or playful styles
✘ Hard-to-read fonts
✘ Heavy animation
✘ Oversized signatures

πŸ›  Tools & Format Flexibility

We allow full creative freedom regarding:

Animation style

Typography choices

Structuring of the two-column layout

How the service lists scroll or cycle

As long as the end result is clean, brand-aligned, professional, and email-compatible.

πŸ’¬ Final Note to Designers

We encourage creativity within the boundaries of corporate professionalism.
This signature will represent our company every time an email is sent β€” it must communicate trust, clarity, expertise, and brand strength.

```html
<!DOCTYPE html>
<html lang="en">
<head>
<meta charset="utf-8">
<title>KAV Fire &amp; Security – Email Signature</title>
<link rel="stylesheet" href="https://fonts.googleapis.com/css2?family=Poppins:wght@400;500;600;700&family=Rubik:wght@600&display=swap">
<style>
  :root {
    --stage: #a3a3a3;
    --card: #ffffff;
    --brand-red: #e0202b;
    --ink: #1c1c1c;
    --text: #4a4a4a;
    --rule: #dcdcdc;
    --soft-grey: #f1f1f2;
    --ring: #1e1e1e;
    --portrait-a: #c9ccd1;
    --portrait-b: #7d8591;
  }
  * { margin: 0; padding: 0; box-sizing: border-box; }
  html, body {
    width: 1200px; height: 541px; overflow: hidden;
    background: var(--stage);
    font-family: "Poppins", Arial, sans-serif;
  }
  .signature {
    position: absolute; left: 105px; top: 105px;
    width: 989px; height: 330px;
    background: var(--card);
    overflow: hidden;
    box-shadow: 0 10px 24px rgba(0,0,0,0.18);
  }
  .backdrop { position: absolute; left: 0; top: 0; }
  .portrait {
    position: absolute; left: 89px; top: 68px;
    width: 184px; height: 184px; border-radius: 50%;
    border: 8px solid var(--card);
    background: radial-gradient(circle at 50% 40%, var(--portrait-a), var(--portrait-b));
  }
  .social {
    position: absolute; left: 92px; top: 265px;
    display: flex; gap: 19px; list-style: none;
  }
  .social li {
    width: 30px; height: 30px; border-radius: 50%;
    background: var(--brand-red);
  }
  .divider {
    position: absolute; left: 374px; top: 33px;
    width: 1px; height: 264px; background: var(--rule);
  }
  .identity {
    position: absolute; left: 443px; top: 10px;
    border-left: 4px solid var(--brand-red);
    padding-left: 13px;
  }
  .identity .name {
    font-family: "Rubik", "Poppins", sans-serif;
    font-weight: 600; font-size: 30px; line-height: 34px;
    color: var(--brand-red);
  }
  .identity .title {
    font-size: 23px; line-height: 28px; color: var(--text);
  }
  .company {
    position: absolute; left: 443px; top: 88px;
    display: flex; align-items: center; gap: 10px;
    font-weight: 700; font-size: 22px; color: var(--brand-red);
  }
  .company .mark {
    width: 26px; height: 26px; border-radius: 50%;
    background: var(--brand-red);
  }
  .license {
    position: absolute; left: 443px; top: 120px;
    font-weight: 600; font-size: 18px; color: var(--ink);
  }
  .contacts {
    position: absolute; left: 447px; top: 160px;
    list-style: none;
  }
  .contacts li {
    display: flex; align-items: center;
    height: 40px; font-size: 24px; color: var(--text);
  }
  .contacts svg { width: 22px; height: 22px; margin-right: 20px; fill: var(--brand-red); }
  .cta {
    position: absolute; left: 483px; top: 280px;
    width: 163px; height: 30px; border-radius: 15px;
    background: var(--brand-red); color: #fff;
    font-weight: 700; font-size: 18px; line-height: 30px;
    text-align: center; letter-spacing: -0.2px;
  }
  .flame-art {
    position: absolute; left: 868px; top: 240px;
    width: 72px; height: 92px;
    border-radius: 50% 50% 8px 8px / 70% 70% 8px 8px;
    background: linear-gradient(180deg, #f4545c, var(--brand-red));
  }
</style>
</head>
<body>
<main class="signature">
  <svg class="backdrop" width="400" height="330" viewBox="0 0 400 330" aria-hidden="true">
    <path d="M37 130 A148 148 0 0 1 333 130" fill="none" stroke="var(--ring)" stroke-width="5"/>
    <circle cx="170" cy="10" r="132" fill="var(--brand-red)"/>
    <circle cx="181" cy="358" r="140" fill="var(--soft-grey)"/>
  </svg>

  <div class="portrait" role="img" aria-label="Circular headshot of the team member"></div>

  <ul class="social" aria-label="Social profiles">
    <li role="img" aria-label="Social profile link 1"></li>
    <li role="img" aria-label="Social profile link 2"></li>
    <li role="img" aria-label="Social profile link 3"></li>
    <li role="img" aria-label="Social profile link 4"></li>
  </ul>

  <div class="divider"></div>

  <header class="identity">
    <h1 class="name">Dana Whitfield</h1>
    <p class="title">Technical Director</p>
  </header>

  <div class="company"><span class="mark"></span>KAV Fire &amp; Security</div>
  <p class="license">License# 52804</p>

  <ul class="contacts">
    <li>
      <svg viewBox="0 0 24 24"><path d="M6.6 10.8a15.1 15.1 0 0 0 6.6 6.6l2.2-2.2c.3-.3.7-.4 1-.2 1.1.4 2.3.6 3.6.6.6 0 1 .4 1 1V20c0 .6-.4 1-1 1A17 17 0 0 1 3 4c0-.6.4-1 1-1h3.5c.6 0 1 .4 1 1 0 1.3.2 2.5.6 3.6.1.3 0 .7-.2 1z"/></svg>
      +1 555 014 2290
    </li>
    <li>
      <svg viewBox="0 0 24 24"><path d="M12 2a7 7 0 0 0-7 7c0 5.2 7 13 7 13s7-7.8 7-13a7 7 0 0 0-7-7zm0 9.5A2.5 2.5 0 1 1 12 6.5a2.5 2.5 0 0 1 0 5z"/></svg>
      384 Pembrook St, Elmridge NJ 07912
    </li>
    <li>
      <svg viewBox="0 0 24 24"><path d="M2 5h20v14H2zm2 2v.5l8 5 8-5V7l-8 5z"/></svg>
      info@kavfiresecurity.com
    </li>
  </ul>

  <div class="cta">SIGNUP NOW</div>

  <div class="flame-art" role="img" aria-label="Red flame decoration"></div>
</main>
</body>
</html>
```